Online Psychiatry business - Business Card

I need a business card design. The target audience is busy professionals of any field (this therapy appeals best to 24-35 year olds). It involves psychiatry by tele-medicine (or video-conference). Nothing on it should be a giveaway that it's about mental health. Professional design with silver or gold as the primary colors appeals to me. The card must be as simple and as uncluttered as possible. Some color and flowing design on the edge of the card appeals to me.
CalmHarborDirect.net should probably appear in the center of the card and stand out, i.e. bold lettering, and easy to read, no cursive, but Ariel Black. Some where below this, should appear "Too Busy to Take Care of Yourself? Think again." Since this isn't office based, I don't think an office address is necessary and limits clutter.
Information that does need to appear is my name: Gerald Mossvane, MD
General phone number: 555-417-8062. I'm hoping to get an 24-hour answering service soon so leave a little room for this. In addition I want to include two email addresses:
CalmHarborDirect@mailbox-example.net and CalmHarbor247@mailbox-example.net
Updates

I like the designs. I would like someone to put the website in bold in the center

 as most have been doing with a smaller font reminder nearby saying "No time" etc.
but I'd like to put my name down in the corner with the rest of the contact material.
Black print against a white or grey background appeals to me, with darker silver artwork near the sides (simple abstract, like wavy lines or something you can one up with that works. 
thanks

I ve tried to provide as much feedback as possible given my time limits, so if you have extra questions, please feel free to email. I tried to attach a file of a business card I really like but make be difficult to actually manufacture. I'm going to send you a link to the photo. The card has a pull tab. There is not much information on the outside. In fact, if you were to design the outside, I would just print : Too Busy to Take Care of Yourself? Think Again.

When you pull the tab the remaining information is on the bottom half of the card. Please don't use the color pink!!!!
http://www.cardgallery-example.org/2009/05/100-clever-print-ideas/
It is the 39th photo on the list, about 2/3ds of the way down the page. It is titled: Faltenkiste

#7 and #16 have an appeal to me, except for the dot patterns
Hope this helps

I'm running out of time and energy. I 've been trying to give do down the list and give  individual feedback but I won't be able to do that anymore.

So if you have any specific questions, write me, and again thank you for all your effort!!

I know i received your files, including your zip files, Pindrel,

but Milo, did you send me the files including ZIP on project 6143907?
thanks

Target Market(s)

Working professionals and executive, attorneys, etc.

Industry/Entity Type

Business

Logo Text

Don't Have Time to Take Care of Yourself? Think Again.

Logo styles of interest
Pictorial/Combination Logo
Wordmark Logo
Font styles to use
Other font styles liked:
• Ariel Black appeals to me the most

Requirements
Must have
• Want to emphasize that the website must be obvious, easily found (The CalmHarborDirect.net)
For that reason i'd like the card to be white, and minimal decoration on one or both sides just to add some style and color
Nice to have
• A Very uncluttered, elegant design, and something that makes it stick in your head-doesn't everyone want the last?
Should not have
• Nothing on the card that give it away that this is about psychiatry, such as brain or other symbol, but also nothing that gives it away as a medical business, such as a stethoscope or red cross or anything.

```html
<!DOCTYPE html>
<html lang="en">
<head>
<meta charset="utf-8">
<title>CalmHarborDirect.net – Business Card</title>
<link rel="stylesheet" href="https://fonts.googleapis.com/css2?family=Arimo:wght@400;700&display=swap">
<style>
  :root {
    --backdrop: #e9e7e3;
    --card-white: #ffffff;
    --card-shade: #e4e4e4;
    --ink-dark: #333333;
    --ink-black: #111111;
    --gold-light: #f7ef9a;
    --gold-mid: #ecd46a;
    --gold-deep: #d9ad2c;
    --gold-text: #e0a21c;
    --swoosh-gray: #4a4a4a;
    --on-gold: #ffffff;
  }
  * { box-sizing: border-box; margin: 0; padding: 0; }
  html, body {
    width: 1200px; height: 418px; overflow: hidden;
    background: var(--backdrop);
    font-family: "Arimo", Arial, sans-serif;
  }
  .canvas { position: relative; width: 1200px; height: 418px; }
  .card {
    position: absolute; top: 90px; width: 466px; height: 266px;
    overflow: hidden;
    box-shadow: 0 3px 10px rgba(0,0,0,0.25);
    text-align: center;
  }
  .card--front {
    left: 122px;
    background: radial-gradient(ellipse at 50% 40%, var(--card-white) 55%, var(--card-shade) 100%);
  }
  .card--back {
    left: 626px;
    background: linear-gradient(170deg, var(--gold-light) 0%, var(--gold-mid) 55%, var(--gold-deep) 100%);
  }
  .edge-wave { position: absolute; left: 0; bottom: 0; width: 466px; height: 266px; }
  .site-name {
    position: absolute; left: 0; right: 0;
    font-weight: 700; line-height: 1;
  }
  .card--front .site-name { top: 62px; font-size: 34px; color: var(--ink-dark); }
  .tagline {
    position: absolute; left: 0; right: 0; top: 105px;
    font-size: 12.5px; color: var(--gold-text);
  }
  .contact { position: absolute; left: 0; right: 0; font-size: 11px; line-height: 14px; color: var(--ink-black); }
  .contact--name { top: 146px; font-size: 12px; font-weight: 700; }
  .contact--phone { top: 165px; }
  .contact--phone strong { font-size: 12.5px; }
  .contact--mail-1 { top: 187px; }
  .contact--mail-2 { top: 203px; }
  .feather-art { position: absolute; right: 0; top: 0; width: 190px; height: 210px; }
  .card--back .site-name {
    top: 93px; font-size: 34px; color: var(--on-gold);
    text-shadow: 0 1px 3px rgba(0,0,0,0.35);
  }
  .back-tagline {
    position: absolute; left: 0; right: 0; top: 139px;
    font-size: 12px; font-weight: 700; color: var(--ink-black); letter-spacing: 0.3px;
  }
  .service-note {
    position: absolute; left: 0; right: 0; top: 225px;
    font-size: 12px; font-weight: 700; color: var(--ink-black);
  }
</style>
</head>
<body>
<main class="canvas">
  <section class="card card--front">
    <svg class="edge-wave" viewBox="0 0 466 266" aria-hidden="true">
      <defs>
        <linearGradient id="goldBand" x1="0" y1="0" x2="1" y2="0">
          <stop offset="0" stop-color="#f8f2a6"/>
          <stop offset="0.5" stop-color="#f0dc7c"/>
          <stop offset="1" stop-color="#dcb233"/>
        </linearGradient>
      </defs>
      <path d="M0,204 C110,264 270,270 466,224 L466,266 L0,266 Z" fill="url(#goldBand)"/>
      <path d="M0,192 C90,238 200,260 310,252 C230,258 100,244 0,202 Z" fill="var(--swoosh-gray)"/>
      <path d="M0,200 C110,258 270,266 466,218" fill="none" stroke="#9a9a9a" stroke-width="1.5"/>
      <path d="M380,228 C410,222 440,216 466,210" fill="none" stroke="#666" stroke-width="2"/>
    </svg>
    <h1 class="site-name">CalmHarborDirect.net</h1>
    <p class="tagline">"You're a amazing person. We should talk again."</p>
    <p class="contact contact--name">Gerald Mossvane, MD</p>
    <p class="contact contact--phone">General Phone: <strong>555-417-8062</strong></p>
    <p class="contact contact--mail-1">CalmHarborDirect@mailbox-example.net</p>
    <p class="contact contact--mail-2">CalmHarbor247@mailbox-example.net</p>
  </section>

  <section class="card card--back">
    <svg class="feather-art" viewBox="0 0 190 210" role="img" aria-label="Soft abstract feather brush decoration">
      <defs>
        <radialGradient id="featherGlow" cx="0.6" cy="0.3" r="0.6">
          <stop offset="0" stop-color="#ffffff" stop-opacity="0.55"/>
          <stop offset="1" stop-color="#ffffff" stop-opacity="0"/>
        </radialGradient>
      </defs>
      <ellipse cx="115" cy="70" rx="95" ry="110" fill="url(#featherGlow)"/>
    </svg>
    <h2 class="site-name">CalmHarborDirect.net</h2>
    <p class="back-tagline">“TOO BUSY TO TAKE CARE OF YOURSELF? THINK AGAIN.”</p>
    <p class="service-note">24-HOUR ANSWERING SERVICE</p>
  </section>
</main>
</body>
</html>
```